Brintel Works - Fast, Efficient and Gas Mainteance for Domestic, Commercial and Industrial clients

We are in the process of purchasing a new business and would like to get a new logo and business card.
Business is a gas maintenance business that also does new gas installations.
Has been established since 1988.
Services include:
Install all types of gas appliances & equipment inc. hot water units
Maintain / repair / replace all types of gas appliances & equipment

Target Market(s)

Domestic, Commercial and Industrial clients

Industry/Entity Type

Business

Contact Information for Business Card

admin@brintelworks.com.au
07 3918 4726
Brintel Works PTY LTD

Logo Text

Gas Fitting & Plumbing Maintenance Specialists

Font styles to use
Sans Serif

Requirements
Must have
• Logo
• Business name, contact number, email address, web address
• Domestic | Commercial | Industrial Est Since 1988
Nice to have
• Possibly a black card with a flame logo to one side
Should not have
• Spelling errors

```html
<!DOCTYPE html>
<html lang="en">
<head>
<meta charset="utf-8">
<title>Brintel Works – Business Card</title>
<link href="https://fonts.googleapis.com/css2?family=Arimo:wght@400;700&display=swap" rel="stylesheet">
<style>
  :root {
    --backdrop: #1d2026;
    --card-deep: #0d4aa5;
    --card-bright: #00aaea;
    --brand-light: #1b9fe0;
    --ink-white: #ffffff;
  }
  * { margin: 0; padding: 0; box-sizing: border-box; }
  html, body {
    width: 1200px; height: 1200px; overflow: hidden;
    background: var(--backdrop);
    font-family: "Arimo", Arial, sans-serif;
  }
  .canvas { position: relative; width: 1200px; height: 1200px; }
  .card {
    position: absolute; left: 214px; width: 803px; height: 447px;
    border-radius: 32px; overflow: hidden;
  }
  .card-front {
    top: 130px;
    background: radial-gradient(ellipse 340px 300px at 48% 52%, var(--card-bright) 0%, #0a78cc 50%, var(--card-deep) 100%);
  }
  .card-back {
    top: 638px;
    background: radial-gradient(ellipse 520px 420px at 92% 85%, var(--card-bright) 0%, #0575c9 40%, var(--card-deep) 75%);
  }
  .front-wordmark {
    position: absolute; left: 0; right: 0; top: 170px;
    text-align: center; color: var(--ink-white);
    font-weight: 700; font-size: 88px; letter-spacing: 1px; line-height: 1;
  }
  .back-brand { position: absolute; left: 82px; top: 246px; width: 218px; }
  .back-wordmark {
    color: var(--brand-light); font-weight: 700; font-size: 50px;
    line-height: 1; letter-spacing: 0; text-align: center;
  }
  .back-company {
    margin-top: 14px; color: var(--ink-white); font-size: 18px;
    word-spacing: 3px; text-align: center;
  }
  .back-tagline {
    position: absolute; left: 80px; top: 377px;
    color: var(--ink-white); font-size: 10px;
  }
  .contact-list { position: absolute; right: 40px; top: 130px; list-style: none; }
  .contact-item {
    display: flex; justify-content: flex-end; align-items: center;
    height: 49px; color: var(--ink-white); font-size: 22px; word-spacing: 3px;
  }
  .contact-icon { width: 24px; height: 24px; margin-left: 22px; flex: none; }
</style>
</head>
<body>
<main class="canvas">
  <section class="card card-front">
    <div class="front-wordmark">BRINTEL</div>
  </section>

  <section class="card card-back">
    <div class="back-brand">
      <div class="back-wordmark">BRINTEL</div>
      <div class="back-company">Brintel Works PTY LTD</div>
    </div>
    <div class="back-tagline">Domestic | Commercial | Industrial Est Since 1988</div>

    <ul class="contact-list">
      <li class="contact-item">Adress 01, Adress, City.
        <svg class="contact-icon" viewBox="0 0 24 24" aria-hidden="true"><path d="M12 3 L1 12 H4 V21 H10 V15 H14 V21 H20 V12 H23 Z" fill="#fff"/></svg>
      </li>
      <li class="contact-item">07 3918 4726
        <svg class="contact-icon" viewBox="0 0 24 24" aria-hidden="true"><path d="M6 2 L10 2 L11 7 L8.5 9 C9.5 12 12 14.5 15 15.5 L17 13 L22 14 L22 18 C22 20 20 22 18 22 C9 21 3 15 2 6 C2 4 4 2 6 2 Z" fill="#fff" transform="scale(0.9) translate(2 1)"/></svg>
      </li>
      <li class="contact-item">admin@brintelworks.com.au
        <svg class="contact-icon" viewBox="0 0 24 24" aria-hidden="true"><circle cx="12" cy="12" r="4" fill="none" stroke="#fff" stroke-width="3"/><path d="M16 8 V14 C16 17 21 17 21 12 A9 9 0 1 0 16 20" fill="none" stroke="#fff" stroke-width="3"/></svg>
      </li>
      <li class="contact-item">www.brintelworks.com.au
        <svg class="contact-icon" viewBox="0 0 24 24" aria-hidden="true"><g fill="none" stroke="#fff" stroke-width="1.8"><circle cx="12" cy="12" r="10"/><ellipse cx="12" cy="12" rx="4.5" ry="10"/><line x1="2" y1="12" x2="22" y2="12"/><line x1="12" y1="2" x2="12" y2="22"/><path d="M4 7 H20 M4 17 H20"/></g></svg>
      </li>
    </ul>
  </section>
</main>
</body>
</html>
```